creation of a business card design for a company specializing in the creation...

I would like to create a design for a professional business card on a black background and with the company's colors (I am attaching some files: including the logo in horizontal and centered format, I am also attaching a recent project design a T-shirt, this is the one I chose to give you an idea of my preferences.

we are in the process of developing a new website design, it is still in the development phase but it can be viewed at the following address: www.vantrelmo.be to give you other ideas about the company
you will see for yourself the subject of my main activity: company specializing in the construction of stairs

I would like a business card that stands out from the rest with a unique design

here is the informations
Name: Lucien Barthel
Function: Manager
Address: Rue Moulinet du Parc 42
7180 La Louvière
telephone: +32 468 219 804
email: info@rx7p.be
website: rx7p. be
social networks: Facebook, YouTube, TikTok, Instagram

Target Market(s)

customer who wants to have a beautiful staircase built

Industry/Entity Type

contruction d'escalier

Contact Information for Business Card

Adresse. Numero de telephone, site web, le texte : "Createur d'escalier", logo recto-verso, icone des reseaux sociaux

Requirements
Must have
• the mention: Stair creator
Nice to have
• an illustration of a designer staircase
Should not have
• do not distort the logo

```html
<!DOCTYPE html>
<html lang="en">
<head>
<meta charset="utf-8">
<title>RX7P Business Card</title>
<link href="https://fonts.googleapis.com/css2?family=Montserrat:wght@300;400;600;700&display=swap" rel="stylesheet">
<style>
  :root {
    --bg: #1c1d20;
    --card: #1e1f22;
    --card-deep: #17181a;
    --ink: #f2f4f6;
    --muted: #9aa0a6;
    --accent: #6f9fc4;
    --accent-soft: #8fb4d2;
    --faint: #2a2b2f;
  }
  * { box-sizing: border-box; margin: 0; padding: 0; }
  html, body { width: 1200px; height: 900px; overflow: hidden; }
  body {
    background: var(--bg);
    font-family: "Montserrat", sans-serif;
    position: relative;
  }
  .card {
    position: absolute;
    left: 230px;
    width: 740px;
    height: 423px;
    border-radius: 26px;
    background: linear-gradient(135deg, var(--card) 0%, var(--card-deep) 100%);
    border-bottom: 5px solid var(--accent);
    overflow: hidden;
    box-shadow: 0 14px 30px rgba(0,0,0,.45);
  }
  .card--front { top: 18px; }
  .card--back { top: 459px; }

  .brand {
    position: absolute;
    display: flex;
    align-items: center;
    gap: 18px;
  }
  .brand__mark {
    width: 58px; height: 58px;
    background: var(--faint);
  }
  .brand__text { display: flex; flex-direction: column; }
  .brand__name {
    font-weight: 300;
    letter-spacing: 10px;
    line-height: 1;
  }
  .brand__tag {
    font-weight: 300;
    letter-spacing: 6px;
    text-transform: uppercase;
    margin-top: 8px;
  }
  .card--front .brand { left: 50%; top: 50%; transform: translate(-50%, -50%); }
  .card--front .brand__name { font-size: 72px; color: #3a3c40; }
  .card--front .brand__tag { font-size: 13px; color: #4a4c51; }

  .card--back .brand { left: 50px; top: 50px; }
  .card--back .brand__mark { width: 46px; height: 46px; background: var(--accent-soft); }
  .card--back .brand__name { font-size: 50px; color: var(--ink); letter-spacing: 8px; }
  .card--back .brand__tag { font-size: 11px; color: var(--accent); letter-spacing: 5px; }

  .tab {
    position: absolute; right: 56px; top: 0;
    width: 26px; height: 46px;
    background: var(--accent);
  }
  .person {
    position: absolute; right: 100px; top: 40px;
    text-align: right;
  }
  .person__name { font-size: 30px; font-weight: 700; color: var(--accent); }
  .person__role { font-size: 15px; color: var(--ink); margin-top: 2px; }

  .watermark {
    position: absolute; right: 40px; top: 170px;
    font-size: 120px; font-weight: 700;
    color: #232428; letter-spacing: 6px;
  }

  .address {
    position: absolute; left: 50px; top: 200px;
    font-size: 17px; color: var(--ink); line-height: 1.3;
  }
  .contacts {
    position: absolute; left: 50px; top: 262px;
    list-style: none;
  }
  .contacts li {
    display: flex; align-items: center; gap: 12px;
    font-size: 17px; color: var(--ink); line-height: 1.6;
  }
  .contacts svg { width: 16px; height: 16px; fill: var(--accent); }
  .socials {
    position: absolute; left: 50px; top: 360px;
    display: flex; gap: 12px;
  }
  .socials span {
    width: 20px; height: 20px; border-radius: 4px;
    background: var(--accent);
  }
</style>
</head>
<body>

<section class="card card--front" aria-label="Card front">
  <div class="brand">
    <div class="brand__mark"></div>
    <div class="brand__text">
      <span class="brand__name">RX7P</span>
      <span class="brand__tag">Stair Creator</span>
    </div>
  </div>
</section>

<section class="card card--back" aria-label="Card back">
  <div class="tab"></div>
  <div class="person">
    <div class="person__name">Lucien Barthel</div>
    <div class="person__role">Manager</div>
  </div>
  <div class="watermark" aria-hidden="true">RX7P</div>

  <div class="brand">
    <div class="brand__mark"></div>
    <div class="brand__text">
      <span class="brand__name">RX7P</span>
      <span class="brand__tag">Stair Creator</span>
    </div>
  </div>

  <p class="address">Rue Moulinet du Parc 42<br>7180 La Louvière</p>

  <ul class="contacts">
    <li>
      <svg viewBox="0 0 24 24" aria-hidden="true"><path d="M6.6 10.8a15 15 0 0 0 6.6 6.6l2.2-2.2a1 1 0 0 1 1-.25 11.4 11.4 0 0 0 3.6.57 1 1 0 0 1 1 1V20a1 1 0 0 1-1 1A17 17 0 0 1 3 4a1 1 0 0 1 1-1h3.5a1 1 0 0 1 1 1c0 1.25.2 2.45.57 3.57a1 1 0 0 1-.25 1z"/></svg>
      +32 468 219 804
    </li>
    <li>
      <svg viewBox="0 0 24 24" aria-hidden="true"><path d="M2 5h20v14H2zm2 2v.5l8 5 8-5V7z"/></svg>
      info@rx7p.be
    </li>
    <li>
      <svg viewBox="0 0 24 24" aria-hidden="true"><path d="M12 2a10 10 0 1 0 0 20 10 10 0 0 0 0-20zm0 2c.9 1.2 1.6 2.6 2 4h-4c.4-1.4 1.1-2.8 2-4zM4.3 14a8 8 0 0 1 0-4h3.4a16 16 0 0 0 0 4zm5.7 0a14 14 0 0 1 0-4h4a14 14 0 0 1 0 4zm6.3 0a16 16 0 0 0 0-4h3.4a8 8 0 0 1 0 4z"/></svg>
      rx7p. be
    </li>
  </ul>

  <div class="socials" role="img" aria-label="Social network links">
    <span></span><span></span><span></span><span></span>
  </div>
</section>

</body>
</html>
```